ONE PAGE WEB DESIGN NEEDED for Finance Company

We need a web design (ONE PAGE DESIGN ONLY) for a new finance website called Tidewell Lending. Tidewell Lending helps customers get the right loan, whether its a home loan, investment loan, business loan etc.

You are required to come up with just the homepage design. Professionalism and quality is the key factors in the successful design.

Here are a few design questions to help you out:

-
What information should be used on the page?
Ive provided a document which outlines all the information needed to put on homepage (attached to the brief - called tidewell_page_info). Also see the Must Have section below on this brief.

-
What links should appear in the navigation/footer?:
The navigation should provide links to the following pages (NOTE: services link has subcategories):
1 Homepage
2 Services
- Home loans
- Investment loans
- Refinancing loans
- Business loans
3 About Us
4 FAQ
5 Contact Us

-
What colors should be used in the design?
Our company colors - Cyan: #2EADE3, Blue: #004B70, White. Feel free to submit designs with slight variations if you feel it improves the design.

-
What should the layout of the page be?
This is up to you to come up with - we are open to different layouts for the page design (as long as they capture the information effectively and making it easy to understand).

Target Market(s)

Potential Home owners, Families and Business Owners

Industry/Entity Type

Business

Requirements
Must have
• - Must contain our logo (attached as PNG and Illustrator file)
- Winning designer must supply a Photoshop file (PSD) that will allow us.
Nice to have
• - Should include photos/images of families, professional groups, tradespeople etc (you can use stock photos from PixaVault and I will purchase them once you are selected as the winning design)
- Link to a loan calculator somewhere on front page with a button 'Find out how much you could borrow' (or maybe even try adding a loan calculator to the homepage if you think this would look good)
- Page should have a main headline "Finding the right loan for you" or "Tidewell Lending finds the right loan for our customers."
- Must include Accreditation logos somewhere on the homepage (will try and supply these soon)
Should not have
• - Poor quality designs will not be considered
- Do not use clipart

```html
<!DOCTYPE html>
<html lang="en">
<head>
<meta charset="utf-8">
<title>Tidewell Lending</title>
<link rel="stylesheet" href="https://fonts.googleapis.com/css2?family=Arimo:wght@400;700&family=Josefin+Slab:wght@300;400&family=PT+Serif&display=swap">
<style>
  :root {
    --cyan: #2eade3;
    --blue: #004b70;
    --ink: #222;
    --rule: #dcdcdc;
    --sky: #cfe9f7;
    --white: #fff;
  }
  * { margin: 0; padding: 0; box-sizing: border-box; }
  html, body { width: 1200px; height: 1200px; overflow: hidden; background: var(--white); }
  body { position: relative; font-family: "Arimo", Arial, sans-serif; color: var(--ink); }
  .abs { position: absolute; }

  .header-sky { left: 0; top: 0; width: 1200px; height: 100px;
    background: linear-gradient(180deg, var(--sky) 0%, #e9f5fc 60%, var(--white) 100%); }
  .brand { left: 130px; top: 20px; }
  .brand-mark { position: absolute; left: 46px; top: 0; width: 42px; height: 42px; border-radius: 50%; border: 4px solid var(--cyan); }
  .brand-name { position: absolute; left: 0; top: 48px; white-space: nowrap; font-size: 20px; font-weight: 700; color: var(--cyan); }

  .main-nav { right: 130px; top: 77px; display: flex; gap: 30px; }
  .main-nav a { font-size: 11px; font-weight: 700; color: var(--blue); text-decoration: none; letter-spacing: .3px; padding-bottom: 8px; }
  .main-nav a.is-current { border-bottom: 3px solid var(--blue); }
  .nav-rule { left: 130px; top: 100px; width: 940px; height: 1px; background: #5b8ca8; }

  .hero-photo { left: 168px; top: 140px; width: 224px; height: 220px; border-radius: 50%;
    background: radial-gradient(circle at 45% 40%, #c99a6a 0%, #7a6a3a 45%, #3f4a2a 100%); }
  .headline { left: 450px; top: 152px; width: 620px; font-family: "Josefin Slab", serif; font-weight: 300;
    font-size: 38px; line-height: 44px; color: var(--cyan); }
  .hero-divider { left: 457px; top: 270px; width: 574px; border-top: 1px dotted #555; }
  .calc-link { left: 620px; top: 320px; display: flex; gap: 26px; }
  .calc-link p { font-size: 14px; font-weight: 700; color: var(--cyan); line-height: 17px; }

  .intro { left: 200px; top: 398px; width: 800px; text-align: center; font-family: "PT Serif", serif; font-size: 14px; line-height: 16px; }
  .intro p { margin-bottom: 8px; }
  .offer { left: 0; top: 525px; width: 1200px; text-align: center; font-family: "PT Serif", serif; font-size: 14.5px; color: var(--blue); }
  .offer-arrow { left: 780px; top: 528px; }

  .loan-col { top: 593px; width: 220px; }
  .loan-head { position: relative; height: 29px; border-bottom: 2px solid var(--cyan); }
  .loan-head svg { position: absolute; left: 0; top: 0; }
  .loan-head h2 { position: absolute; left: 60px; top: 4px; font-family: "Josefin Slab", serif; font-weight: 400; font-size: 14px; color: var(--cyan); }
  .loan-list { list-style: none; margin-top: 15px; font-size: 12px; }
  .loan-list li { height: 21px; padding-left: 20px; position: relative; }
  .loan-list li::before { content: "····›"; position: absolute; left: 0; top: -1px; font-size: 10px; color: #333; letter-spacing: -1px; }
  .loan-list li.label { padding-left: 0; font-weight: 700; }
  .loan-list li.label::before { content: none; }

  .panel-note { left: 200px; top: 758px; width: 800px; text-align: center; font-family: "PT Serif", serif; font-size: 14px; line-height: 16px; }
  .contact-line { left: 0; top: 797px; width: 1200px; text-align: center; font-family: "PT Serif", serif; font-size: 14.5px; color: var(--blue); }

  .accreditation { left: 130px; top: 850px; width: 940px; height: 100px; border: 1px solid var(--rule); }
  .accreditation-title { position: absolute; left: -1px; top: -1px; width: 221px; height: 100px; background: var(--cyan);
    color: var(--white); font-family: "PT Serif", serif; font-size: 19px; padding: 16px 20px; }
  .accreditation-badge { position: absolute; top: 34px; width: 100px; height: 26px; border-radius: 4px; background: #b8b8b8; }
  .accreditation-sep { position: absolute; top: 9px; width: 1px; height: 80px; background: var(--rule); }

  .footer-rule { left: 130px; top: 990px; width: 940px; height: 2px; background: var(--cyan); }
  .footer-links { left: 130px; top: 1008px; font-size: 11px; line-height: 20px; }
  .social { left: 930px; top: 1010px; display: flex; gap: 15px; }
  .social span { width: 25px; height: 25px; border-radius: 50%; background: var(--cyan); }
</style>
</head>
<body>
  <div class="abs header-sky"></div>
  <div class="abs brand"><span class="brand-mark"></span><span class="brand-name">Tidewell Lending</span></div>
  <nav class="abs main-nav">
    <a class="is-current" href="#">HOME</a><a href="#">SERVICES</a><a href="#">ABOUT US</a><a href="#">FAQ</a><a href="#">CONTACT US</a>
  </nav>
  <div class="abs nav-rule"></div>

  <div class="abs hero-photo" role="img" aria-label="Photo of a smiling family with a toddler sitting outdoors"></div>
  <h1 class="abs headline">Tidewell Lending finds the right loan for our customers.</h1>
  <div class="abs hero-divider"></div>
  <div class="abs calc-link">
    <svg width="22" height="28" viewBox="0 0 22 28"><rect x="1" y="1" width="18" height="26" rx="2" fill="none" stroke="#2eade3" stroke-width="2"/><rect x="4" y="4" width="12" height="5" fill="none" stroke="#2eade3" stroke-width="1.5"/><g fill="#2eade3"><rect x="4" y="12" width="3" height="3"/><rect x="9" y="12" width="3" height="3"/><rect x="14" y="12" width="3" height="3"/><rect x="4" y="17" width="3" height="3"/><rect x="9" y="17" width="3" height="3"/><rect x="14" y="17" width="3" height="3"/><rect x="4" y="22" width="3" height="3"/><rect x="9" y="22" width="3" height="3"/><rect x="14" y="22" width="3" height="3"/></g></svg>
    <p>Find out how much you could<br>borrow <svg width="16" height="12" viewBox="0 0 16 12"><path d="M2 1l5 5-5 5M8 1l5 5-5 5" fill="none" stroke="#2eade3" stroke-width="2.2"/></svg></p>
  </div>

  <div class="abs intro">
    <p>At Tidewell Lending we work hard to find the right loan for our customers. We do that because we are backed by sound industry knowledge, professional experience and a great customer service approach.</p>
    <p>Tidewell Lending guarantees that we will always tailor the best solution for your individual lending needs.</p>
    <p>We can do that because we have access to a wide variety of lending options from major banks to non-bank lenders and we are committed to finding the right lending product for you.</p>
  </div>
  <p class="abs offer">We offer a unique approach to help you find the right:</p>
  <svg class="abs offer-arrow" width="50" height="34" viewBox="0 0 50 34"><path d="M2 6C20 -2 38 4 42 26" fill="none" stroke="#8fb3c6" stroke-width="2"/><path d="M35 22l7 10 5-11" fill="none" stroke="#8fb3c6" stroke-width="2"/></svg>

  <section class="abs loan-col" style="left:130px">
    <div class="loan-head"><svg width="50" height="29"><path d="M2 29A23 23 0 0 1 48 29" fill="none" stroke="#2eade3" stroke-width="2"/><path d="M14 27v-8l8-6 8 6v8z" fill="#2eade3"/><circle cx="30" cy="17" r="5" fill="#2eade3" stroke="#fff"/></svg><h2>Home Loan</h2></div>
    <ul class="loan-list"><li>Home buyers</li><li>First home buyers</li><li>Over 20 lenders</li></ul>
  </section>
  <section class="abs loan-col" style="left:370px">
    <div class="loan-head"><svg width="50" height="29"><path d="M2 29A23 23 0 0 1 48 29" fill="none" stroke="#2eade3" stroke-width="2"/><g fill="#2eade3"><rect x="12" y="24" width="14" height="2"/><rect x="14" y="20" width="12" height="2"/><rect x="16" y="16" width="10" height="2"/><rect x="18" y="12" width="8" height="2"/></g><circle cx="32" cy="22" r="4" fill="none" stroke="#2eade3" stroke-width="2"/></svg><h2>Investment Loan</h2></div>
    <ul class="loan-list"><li>Property investment loans</li><li>Interest only loans</li></ul>
  </section>
  <section class="abs loan-col" style="left:610px">
    <div class="loan-head"><svg width="50" height="29"><path d="M2 29A23 23 0 0 1 48 29" fill="none" stroke="#2eade3" stroke-width="2"/><g fill="#2eade3"><rect x="14" y="21" width="3" height="6"/><rect x="19" y="18" width="3" height="9"/><rect x="24" y="15" width="3" height="12"/><rect x="29" y="12" width="3" height="15"/></g><path d="M12 18l8-6 5 3 9-7" fill="none" stroke="#2eade3" stroke-width="2"/></svg><h2>Refinancing</h2></div>
    <ul class="loan-list"><li>Refinancing for the best rate</li><li>Upsizing or downsizing</li><li>Change from a variable to a fixed rate</li></ul>
  </section>
  <section class="abs loan-col" style="left:850px">
    <div class="loan-head"><svg width="50" height="29"><path d="M2 29A23 23 0 0 1 48 29" fill="none" stroke="#2eade3" stroke-width="2"/><path d="M16 27V11h10l4 4v12z" fill="none" stroke="#2eade3" stroke-width="2"/><circle cx="28" cy="23" r="4.5" fill="#fff" stroke="#2eade3" stroke-width="1.5"/></svg><h2>Business Loan</h2></div>
    <ul class="loan-list"><li class="label">Business Finance</li><li>Long term</li><li>Short term</li><li>Equipment and Leasing</li></ul>
  </section>

  <p class="abs panel-note">There are many different loan products in the marketplace. Tidewell Lending has access to a wide panel of lenders which means we can access bank and non-bank lenders that meet the individual needs of our customers.</p>
  <p class="abs contact-line">Contact Tidewell Lending today on: 1800 555 014 to find out more. <svg width="22" height="22" viewBox="0 0 22 22" style="vertical-align:-5px"><path d="M5 8a7 7 0 0 1 12-1M17 14a7 7 0 0 1-12 1" fill="none" stroke="#b9cdd8" stroke-width="2"/><path d="M17 3v4h-4M5 19v-4h4" fill="none" stroke="#b9cdd8" stroke-width="2"/></svg></p>

  <section class="abs accreditation">
    <h2 class="accreditation-title" style="font-weight:400">Accreditation logos</h2>
    <span class="accreditation-badge" style="left:300px"></span>
    <span class="accreditation-sep" style="left:470px"></span>
    <span class="accreditation-badge" style="left:540px"></span>
    <span class="accreditation-sep" style="left:709px"></span>
    <span class="accreditation-badge" style="left:775px"></span>
  </section>

  <div class="abs footer-rule"></div>
  <footer class="abs footer-links">
    <p>Terms of Use | Legal notice | Sitemap | Disclaimer</p>
    <p>Copyright © 2012 Tidewell Lending.&nbsp; All rights reserved.</p>
  </footer>
  <div class="abs social" aria-label="Social links"><span></span><span></span><span></span><span></span></div>
</body>
</html>
```